Local fast-growing company in the service sector

We are looking for a modern business card design, which should also appear on our letterheads

Target Market(s)

Private and industrial sectors

Contact Information for Business Card

Vorname Name
Kellberger Str. 18
73614 Lindenhof
Tel.: 07146-839214-0
Name@agentur-kvtl.de

Colors
9d9d9d
919191
aaaaaa

Requirements
Must have
• The logo (file) in silver

```html
<!DOCTYPE html>
<html lang="de">
<head>
<meta charset="utf-8">
<title>KVTL Visitenkarte</title>
<link rel="stylesheet" href="https://fonts.googleapis.com/css2?family=Open+Sans:wght@400;700&display=swap">
<style>
  :root {
    --stage: #1f1f1f;
    --card: #ffffff;
    --card-back: #ececec;
    --silver: #9d9d9d;
    --silver-mid: #919191;
    --silver-light: #aaaaaa;
    --ink: #4a4a4a;
  }
  * { margin: 0; padding: 0; box-sizing: border-box; }
  html, body { width: 1200px; height: 900px; overflow: hidden; }
  body {
    background: var(--stage);
    font-family: "Open Sans", sans-serif;
    position: relative;
  }
  .card {
    position: absolute;
    width: 560px;
    height: 320px;
    border-radius: 4px;
    overflow: hidden;
  }
  .card-front { left: 50px; top: 110px; background: var(--card); }
  .card-back {
    left: 590px; top: 470px;
    background: linear-gradient(135deg, #f7f7f7 0%, var(--card-back) 100%);
  }
  .brand { display: flex; align-items: center; gap: 14px; position: absolute; }
  .brand-mark { width: 34px; height: 34px; background: var(--silver-light); flex: none; }
  .brand-text { color: var(--silver); font-weight: 700; line-height: 1; }
  .brand-name { font-size: 52px; letter-spacing: 1px; }
  .brand-url { font-size: 17px; letter-spacing: 2px; margin-top: 4px; }
  .card-front .brand { left: 40px; top: 48px; }
  .card-back .brand { left: 200px; top: 110px; }
  .card-back .brand-name { font-size: 64px; }
  .card-back .brand-url { font-size: 21px; }
  .ribbon-area {
    position: absolute;
    background: linear-gradient(160deg, #f4f4f4 0%, #d2d2d2 60%, #e8e8e8 100%);
    border-radius: 12px;
  }
  .card-front .ribbon-area { right: 24px; top: 20px; width: 110px; height: 150px; }
  .card-back .ribbon-area { left: 0; bottom: 40px; width: 170px; height: 190px; border-radius: 0 14px 14px 0; }
  .contact { position: absolute; left: 190px; top: 170px; color: var(--ink); }
  .person { font-size: 21px; font-weight: 700; margin-bottom: 12px; }
  .contact-list { list-style: none; font-size: 13px; }
  .contact-list li { display: flex; align-items: center; gap: 7px; margin-bottom: 4px; white-space: nowrap; }
  .icon { width: 14px; height: 14px; flex: none; }
</style>
</head>
<body>
  <section class="card card-front">
    <div class="brand">
      <span class="brand-mark"></span>
      <div class="brand-text">
        <div class="brand-name">KVTL</div>
        <div class="brand-url">agentur-kvtl.de</div>
      </div>
    </div>
    <div class="ribbon-area" role="img" aria-label="Silberne Bandgrafik als Dekoration"></div>
    <div class="contact">
      <p class="person">Vorname Name</p>
      <ul class="contact-list">
        <li>
          <svg class="icon" viewBox="0 0 14 14"><circle cx="7" cy="7" r="7" fill="#9d9d9d"/><path d="M4.5 3.8l1.3-.3.8 1.8-.9.7a5 5 0 0 0 2.3 2.3l.7-.9 1.8.8-.3 1.3c-3 .3-6-2.7-5.7-5.7z" fill="#fff"/></svg>
          07146-839214-0
        </li>
        <li>
          <svg class="icon" viewBox="0 0 14 14"><circle cx="7" cy="7" r="7" fill="#9d9d9d"/><rect x="3.5" y="4.5" width="7" height="5" fill="#fff"/><path d="M3.5 4.5L7 7.3l3.5-2.8" stroke="#9d9d9d" stroke-width=".8" fill="none"/></svg>
          Name@agentur-kvtl.de
        </li>
        <li>
          <svg class="icon" viewBox="0 0 14 14"><circle cx="7" cy="7" r="7" fill="#9d9d9d"/><path d="M7 3a2.6 2.6 0 0 0-2.6 2.6C4.4 7.6 7 11 7 11s2.6-3.4 2.6-5.4A2.6 2.6 0 0 0 7 3z" fill="#fff"/><circle cx="7" cy="5.6" r="1" fill="#9d9d9d"/></svg>
          Kellberger Str. 18, 73614 Lindenhof
        </li>
      </ul>
    </div>
  </section>

  <section class="card card-back">
    <div class="ribbon-area" role="img" aria-label="Silberne Bandgrafik als Dekoration"></div>
    <div class="brand">
      <span class="brand-mark"></span>
      <div class="brand-text">
        <div class="brand-name">KVTL</div>
        <div class="brand-url">agentur-kvtl.de</div>
      </div>
    </div>
  </section>
</body>
</html>
```